Fun relaxed Travel Photography Business Card*

Require a fun, funky and quirky but rememberable business card for a travel photographer

Industry/Entity Type

Photographer

Contact Information for Business Card

Front Card

(my name) Lenn D.

Travel Photographer ( small under travel photographer) “self-proclaimed”

(website logo) wanderingsoflenn.net

(Instagram logo) @wanderings_of_lenn

(Instagram logo) @wanderings_of_lenn_2.0 (backup for when Instagram puts Lenn on timeout for bad behaviour)

Tel: N/A (removing the potential awkwardness of me not replying)

Email: (see above)

Back Card

Offending people since 1986

(Bottom right corner) “p.s. travelling made me fatTER”

Font styles to use
Serif

Colors

Designer to choose colors to be used in the design.

Requirements
Must have
• a camera
• a similar cartoon version of me as the "logo" see attached files, try to make as similar as possible

```html
<!DOCTYPE html>
<html lang="en">
<head>
<meta charset="utf-8">
<title>Lenn D. – Travel Photographer Business Card</title>
<link rel="stylesheet" href="https://fonts.googleapis.com/css2?family=Open+Sans:wght@400;600&display=swap">
<style>
  :root {
    --backdrop: #202124;
    --card: #2c5470;
    --ink: #ffffff;
    --ink-soft: #e8eef2;
    --art-sun: #f2b53a;
    --art-deep: #c9802a;
    --art-shirt: #2e3f78;
  }
  * { box-sizing: border-box; margin: 0; padding: 0; }
  html, body {
    width: 1200px; height: 1200px; overflow: hidden;
    background: var(--backdrop);
    font-family: "Open Sans", Arial, sans-serif;
    color: var(--ink);
  }
  .sheet { position: relative; width: 1200px; height: 1200px; }
  .card {
    position: absolute; left: 120px;
    width: 960px; height: 548px;
    background: var(--card);
    border-radius: 6px;
    overflow: hidden;
  }
  .card--front { top: 40px; }
  .card--back { top: 612px; }

  /* Front */
  .identity { position: absolute; left: 64px; top: 232px; line-height: 1.12; }
  .identity__name { font-size: 34px; font-weight: 400; letter-spacing: 2px; }
  .identity__role { font-size: 25px; font-weight: 400; letter-spacing: 0.5px; }
  .identity__note { font-size: 18px; color: var(--ink-soft); }

  .contacts { position: absolute; left: 64px; top: 362px; list-style: none; }
  .contacts__item { display: flex; align-items: center; gap: 12px; font-size: 18px; height: 31px; }
  .contacts__icon { width: 16px; height: 16px; flex: none; }

  .baseline {
    position: absolute; left: 64px; right: 60px; top: 474px;
    height: 2px; background: var(--ink);
  }
  .portrait {
    position: absolute; left: 470px; top: 58px;
    width: 400px; height: 416px;
    border-radius: 40px 60px 0 0;
    background: radial-gradient(circle at 35% 55%, var(--art-shirt) 0 18%, transparent 19%),
                linear-gradient(160deg, var(--art-sun), var(--art-deep));
  }

  /* Back */
  .tagline {
    position: absolute; left: 0; right: 0; top: 50%;
    transform: translateY(-50%);
    text-align: center; font-size: 40px; font-weight: 400; letter-spacing: 1px;
  }
  .postscript { position: absolute; right: 56px; bottom: 52px; font-size: 18px; }
</style>
</head>
<body>
<main class="sheet">
  <section class="card card--front" aria-label="Card front">
    <div class="identity">
      <h1 class="identity__name">LENN D.</h1>
      <p class="identity__role">TRAVEL PHOTOGRAPHER</p>
      <p class="identity__note">self-proclaimed</p>
    </div>

    <ul class="contacts">
      <li class="contacts__item">
        <svg class="contacts__icon" viewBox="0 0 16 16" aria-hidden="true">
          <circle cx="8" cy="8" r="7" fill="none" stroke="#fff" stroke-width="1.4"/>
          <ellipse cx="8" cy="8" rx="3" ry="7" fill="none" stroke="#fff" stroke-width="1.2"/>
          <line x1="1" y1="8" x2="15" y2="8" stroke="#fff" stroke-width="1.2"/>
        </svg>
        wanderingsoflenn.net
      </li>
      <li class="contacts__item">
        <svg class="contacts__icon" viewBox="0 0 16 16" aria-hidden="true">
          <rect x="1" y="1" width="14" height="14" fill="none" stroke="#fff" stroke-width="1.4"/>
        </svg>
        @wanderings_of_lenn
      </li>
      <li class="contacts__item">
        <svg class="contacts__icon" viewBox="0 0 16 16" aria-hidden="true">
          <rect x="1" y="1" width="14" height="14" fill="none" stroke="#fff" stroke-width="1.4"/>
        </svg>
        @wanderings_of_lenn_2.0
      </li>
    </ul>

    <div class="portrait" role="img" aria-label="Cartoon illustration of the photographer in sunglasses and a floral shirt lounging on a yellow armchair beside a small table with a drink"></div>
    <div class="baseline"></div>
  </section>

  <section class="card card--back" aria-label="Card back">
    <p class="tagline">OFFENDING PEOPLE SINCE 1986</p>
    <p class="postscript">p.s. travelling made me fatTER</p>
  </section>
</main>
</body>
</html>
```